Business Card Design

Electronic Security Installation Specialists

Check out our website at www.tallbrookllc.com to see what we do.

Industry/Entity Type

Business

Contact Information for Business Card

Tall Brook
Marjorie Hadley
281 Orchard Rise
Mapleton, WV 25871

Colors
3176b5
0455a3
ffffff

```html
<!DOCTYPE html>
<html lang="en">
<head>
<meta charset="utf-8">
<title>Tall Brook Business Card</title>
<link rel="stylesheet" href="https://fonts.googleapis.com/css2?family=Open+Sans:wght@400;600;700&display=swap">
<style>
  :root {
    --brand-blue: #0455a3;
    --brand-blue-light: #3176b5;
    --brand-blue-deep: #1d4590;
    --swoosh-grey: #9a9b9e;
    --card-white: #ffffff;
    --page-bg: #e9ebee;
    --ink-white: #ffffff;
  }
  * { box-sizing: border-box; margin: 0; padding: 0; }
  html, body {
    width: 1200px; height: 900px; overflow: hidden;
    background: var(--page-bg);
    font-family: "Open Sans", Arial, sans-serif;
  }
  .canvas {
    position: relative; width: 1200px; height: 900px;
    display: flex; flex-direction: column; align-items: center;
    justify-content: center; gap: 40px;
  }
  .card {
    position: relative; width: 700px; height: 400px;
    border-radius: 36px; overflow: hidden;
    background: var(--card-white);
    box-shadow: 0 6px 20px rgba(0,0,0,0.12);
  }
  .card-art { position: absolute; inset: 0; }
  .identity { position: absolute; left: 46px; top: 40px; color: var(--ink-white); }
  .identity .name { font-weight: 700; font-size: 27px; line-height: 1.2; }
  .identity .role { font-weight: 400; font-size: 21px; line-height: 1.2; }
  .contact-list {
    position: absolute; left: 46px; top: 158px; list-style: none;
    color: var(--ink-white); font-size: 15.5px; line-height: 1.55;
  }
  .contact-list li { display: flex; align-items: flex-start; gap: 9px; }
  .contact-list svg { flex: none; margin-top: 4px; }
  .brand-seal {
    position: absolute; width: 132px; height: 132px; border-radius: 50%;
    background: var(--brand-blue); border: 4px solid var(--card-white);
    box-shadow: 0 0 0 2px var(--swoosh-grey);
    display: flex; align-items: center; justify-content: center;
    color: var(--ink-white); font-weight: 600; font-size: 22px; text-align: center;
  }
  .card-front .brand-seal { left: 494px; top: 230px; }
  .card-back .brand-seal { left: 300px; top: 40px; width: 100px; height: 100px; font-size: 17px; }
</style>
</head>
<body>
<main class="canvas">

  <section class="card card-front" aria-label="Card front">
    <svg class="card-art" viewBox="0 0 700 400" width="700" height="400" aria-hidden="true">
      <defs>
        <radialGradient id="blueGlow" cx="0.5" cy="0.35" r="0.7">
          <stop offset="0" stop-color="#3176b5"/>
          <stop offset="1" stop-color="#1d4590"/>
        </radialGradient>
      </defs>
      <path d="M0 0 H700 V150 C540,120 330,190 210,400 H0 Z" fill="url(#blueGlow)"/>
      <path d="M700 150 C540,120 330,190 210,400 H258 C360,240 520,165 700,160 Z" fill="var(--swoosh-grey)"/>
    </svg>

    <div class="identity">
      <p class="name">Marjorie Hadley</p>
      <p class="role">Owner / C.E.O</p>
    </div>

    <ul class="contact-list">
      <li>
        <svg width="13" height="13" viewBox="0 0 13 13"><circle cx="6.5" cy="6.5" r="6.5" fill="#fff"/><path d="M6.5 3 a2 2 0 0 1 2 2 c0 1.5 -2 4 -2 4 s-2 -2.5 -2 -4 a2 2 0 0 1 2 -2z" fill="var(--brand-blue)"/></svg>
        <span>281 Orchard Rise,<br>Mapleton, WV 25871</span>
      </li>
      <li>
        <svg width="13" height="13" viewBox="0 0 13 13"><circle cx="6.5" cy="6.5" r="6.5" fill="#fff"/><path d="M4 3.5 l1.5 0 l0.6 1.8 l-0.9 0.7 a5 5 0 0 0 1.8 1.8 l0.7 -0.9 l1.8 0.6 l0 1.5 a5.5 5.5 0 0 1 -5.5 -5.5z" fill="var(--brand-blue)"/></svg>
        <span>304-555-0142</span>
      </li>
      <li>
        <svg width="13" height="13" viewBox="0 0 13 13"><circle cx="6.5" cy="6.5" r="6.5" fill="#fff"/><rect x="4.5" y="3" width="4" height="7" rx="0.8" fill="var(--brand-blue)"/></svg>
        <span>304-555-0187</span>
      </li>
      <li>
        <svg width="13" height="13" viewBox="0 0 13 13"><circle cx="6.5" cy="6.5" r="6.5" fill="#fff"/><rect x="3.5" y="5" width="6" height="4" fill="var(--brand-blue)"/><rect x="4.5" y="3" width="4" height="2" fill="var(--brand-blue)"/></svg>
        <span>304-555-0119</span>
      </li>
      <li>
        <svg width="13" height="13" viewBox="0 0 13 13"><circle cx="6.5" cy="6.5" r="6.5" fill="#fff"/><rect x="3" y="4" width="7" height="5" fill="var(--brand-blue)"/><path d="M3 4 l3.5 3 l3.5 -3" stroke="#fff" stroke-width="0.8" fill="none"/></svg>
        <span>info@tallbrookllc.com</span>
      </li>
      <li>
        <svg width="13" height="13" viewBox="0 0 13 13"><circle cx="6.5" cy="6.5" r="6.5" fill="#fff"/><circle cx="6.5" cy="6.5" r="3.5" stroke="var(--brand-blue)" stroke-width="1" fill="none"/><path d="M3 6.5 H10 M6.5 3 V10" stroke="var(--brand-blue)" stroke-width="0.8"/></svg>
        <span>www.tallbrookllc.com</span>
      </li>
    </ul>

    <div class="brand-seal">Tall Brook</div>
  </section>

  <section class="card card-back" aria-label="Card back">
    <div class="brand-seal">Tall Brook</div>
  </section>

</main>
</body>
</html>
```